Agrarhandel benötigt Homepage
Zielgruppe
Wir sind ein Agrarhandel mit einem Warenumschlagslager im Sinne eines klassischen Einzelhandels und vertreiben Produkte an Landwirte.
Wir vertreiben folgende Hauptproduktgruppen:
Einzelfuttermittel
wie z.B. Sojaexktraktionsschrot. Die einzelnen Produkte könnten z.B. wie die Futtermittel auf folgender Seite dargestellt werden (https://www.kornprobe-beispiel.eu/de/produkt/trelomixan)
Mischfuttermittel
Hier bieten wir unseren Kunden an, individuelles Mischfutter auf Basis unserer Einzelfuttermittel herzustellen.
Weitere Details und weitere Produktbereiche habe ich in einer Powerpoint-Übersicht dargestellt.
Neben diesen Produkten wollen wir uns als Familienunternehmen selbst vorstellen. Zudem betreiben wir in unserer Familie zusätzlich einen Milchviehbetrieb den wir ebenfalls hervorheben möchten, da wir unseren Kunden gegenüber einerseits als Zulieferer aber auch als Kollege auftreten wollen.
Einzelfuttermittel: Hier können wir durch unsere Unabhängigkeit punkten, da wir nicht abhängig von bestimmten Lieferanten sind und dementsprechend unabhängig beraten können. Wir untersuchen im Vergleich zu unseren Wettbewerben die Qualität der Futtermittel bis ins Detail und können daher eine Transparenz bieten, die Konkurrenten in der Regel nicht bieten können. Unser Warenumschlagsplatz mit moderner Technik ermöglicht es uns äußerst kosteneffizient die Waren umschlagen und ausliefern zu können.
Mischfuttermittel: Auf Basis der vorhandenen Einzelfuttermittel stellen wir je nach Kundenwunsch individuelle Mischfutter her. Wir arbeiten mit offenen Deklarationen, sodass unsere Kunden jederzeit nachvollziehen können, ob auch die Einzelfuttermittel verwendet wurden, die sie bestellt haben und keine billigen Ersatzprodukte verwendet wurden.
Zudem sind wir BT und HUPA zertifiziert. Die aktuellen für unser Unternehmen ausgestellten Zertifikate müssen für unsere Kunden als Download zur Verfügung stehen. Statt dem HUPA-Logo bitte das ..
Aufgabenstellung
Wir möchten gerne ein zeitgemäße Homepage, jedoch muss auch berücksichtigt werden, dass unsere Kunden eher konservativ denken.

```html
<!DOCTYPE html>
<html lang="de">
<head>
<meta charset="utf-8">
<title>Kornhaus Agrarhandel</title>
<link href="https://fonts.googleapis.com/css2?family=Inter:wght@400;500;600;700;800;900&display=swap" rel="stylesheet">
<style>
:root{
  --dark:#131210;
  --section:#232323;
  --yellow:#f3cc1f;
  --orange:#f3b40f;
  --grey:#d9d9d9;
  --white:#ffffff;
  --black:#111111;
}
*{margin:0;padding:0;box-sizing:border-box}
html,body{width:688px;height:1200px;overflow:hidden;background:var(--white)}
body{position:relative;font-family:"Inter",sans-serif;color:var(--black)}
.abs{position:absolute}

/* header */
.header-accent{left:0;top:0;width:40px;height:66px;background:var(--orange)}
.header-gap{left:40px;top:0;width:9px;height:66px;background:var(--grey)}
.header{left:49px;top:0;width:639px;height:66px;background:var(--dark)}
.brand{left:60px;top:25px;font-weight:800;font-size:19px;color:#1d5c94;letter-spacing:.2px}
.nav{right:46px;top:31px;display:flex;gap:9px;font-size:7.6px;font-weight:700;color:var(--white)}
.nav .active{color:var(--orange)}
.search{left:656px;top:28px}
.header-line{left:0;top:66px;width:688px;height:5px;background:var(--grey)}

/* hero */
.hero{left:0;top:77px;width:688px;height:198px;background:linear-gradient(180deg,#a48a4a 0%,#8c7038 30%,#6f5a26 55%,#7a5a2c 100%)}
.hero-kicker{left:0;top:109px;width:700px;text-align:center;font-size:9.5px;color:var(--white)}
.hero-title{left:0;top:123px;width:688px;text-align:center;font-size:19.5px;font-weight:900;color:var(--orange);letter-spacing:-.2px}
.hero-sub{left:0;top:152px;width:688px;text-align:center;font-size:7.2px;font-weight:800;color:var(--white);line-height:9px}
.hero-btn{left:318px;top:178px;width:52px;height:14px;border-radius:7px;background:var(--yellow)}
.tile{top:232px;width:113px;height:77px}
.tile-1{left:168px;background:linear-gradient(135deg,#c9832e,#e6b556 50%,#a45a25)}
.tile-2{left:288px;background:linear-gradient(180deg,#c9d7d9 0%,#b5a063 40%,#9a7a3a 100%)}
.tile-3{left:407px;background:linear-gradient(135deg,#d9a04b,#b4762e 55%,#8a5618)}

/* intro */
.intro-title{left:168px;top:346px;width:150px;font-size:13.6px;font-weight:700;line-height:16.4px}
.intro-box{left:328px;top:330px}
.intro-text{left:355px;top:349px;width:160px;font-size:7.3px;color:var(--white);line-height:9.2px}
.intro-text p+p{margin-top:3px}

/* why */
.why-bg{left:0;top:463px}
.why-title{left:167px;top:493px;font-size:17.5px;font-weight:500;color:var(--white)}
.why-lead{left:165px;top:525px;width:240px;font-size:5.6px;color:var(--white);line-height:7px}
.feature{width:100px;color:var(--white)}
.feature .dot{position:absolute;left:0;top:0;width:11px;height:11px;border-radius:50%;background:var(--yellow)}
.feature h3{margin-left:18px;font-size:5.8px;font-weight:600;margin-top:1px}
.feature p{margin-left:18px;margin-top:4px;font-size:5.2px;line-height:6.2px}
.why-btn{left:302px;top:646px;width:53px;height:14px;border-radius:7px;background:var(--yellow)}
.why-frame{left:424px;top:494px;width:234px;height:158px;border:3px solid var(--yellow);border-left:none;border-bottom:none;border-radius:7px;background:var(--yellow)}
.why-photo{left:416px;top:502px;width:235px;height:159px;background:linear-gradient(160deg,#4a3a28 0%,#b07636 40%,#d79a4c 60%,#8a5822 100%)}

/* testimonials */
.testi-title{left:0;top:736px;width:688px;text-align:center;font-size:16px;font-weight:600}
.testi-svg{left:0;top:780px}
.testi-text{left:206px;top:841px;width:290px;font-size:7.3px;color:var(--white);line-height:9px}
.testi-text p+p{margin-top:2px}
.avatar{width:50px;height:50px;border-radius:50%;background:#e8e8e8;border:2px solid var(--white);box-shadow:0 0 2px rgba(0,0,0,.3)}
.pager{top:927px;width:35px;height:5px;border-radius:3px;background:var(--yellow)}
.pager.current{background:var(--section)}

/* footer */
.footer{left:0;top:982px;width:688px;height:188px;background:var(--section)}
.vline{top:1018px;width:1px;height:84px;background:var(--white)}
.vdot{width:5px;height:5px;border-radius:50%;background:var(--white)}
.contact-title{left:226px;top:1018px;font-size:11px;font-weight:500;color:var(--white)}
.field{height:13px;background:var(--grey);font-size:5.6px;font-weight:500;padding:4px 5px;color:#222}
.send{left:389px;top:1071px;width:73px;height:13px;border-radius:3px;background:var(--yellow);font-size:6.6px;font-weight:500;text-align:center;padding-top:2.5px}
.info{left:503px;top:1047px;font-size:6.2px;color:var(--white);line-height:10.6px}
.info li{list-style:none;display:flex;align-items:center;gap:5px}
.foot-brand{left:0;top:1110px;width:688px;text-align:center;font-size:19px;font-weight:800;color:#1d5c94}
.social{top:1149px;width:11px;height:11px;border-radius:2px;background:var(--white)}
.copy{left:0;top:1170px;width:688px;height:30px;background:var(--yellow);text-align:center;font-size:6.6px;font-weight:500;padding-top:11px;color:#222}
</style>
</head>
<body>

<div class="abs header-accent"></div>
<div class="abs header-gap"></div>
<header class="abs header"></header>
<div class="abs brand">Kornhaus</div>
<nav class="abs nav">
  <span class="active">LANDWIRT</span><span>GESCHÄFTSPARTNER</span><span>LIEFERANTEN</span><span>PRODUKTE</span><span>FIRMENPRÄSENTATION</span>
</nav>
<svg class="abs search" width="14" height="14" viewBox="0 0 14 14"><circle cx="5.5" cy="5.5" r="4.3" fill="none" stroke="#fff" stroke-width="1.3"/><line x1="8.6" y1="8.6" x2="13" y2="13" stroke="#fff" stroke-width="1.5"/></svg>
<div class="abs header-line"></div>

<section class="abs hero" role="img" aria-label="Getreidefeld im warmen Abendlicht mit Baumreihe am Horizont"></section>
<div class="abs hero-kicker">LOREM IPSUM</div>
<h1 class="abs hero-title">CONSECTETUR ADIPISCING ELIT</h1>
<p class="abs hero-sub">Excepteur sint occaecat cupidatat non proident, sunt in<br>culpa qui officia deserunt mollit anim id es</p>
<div class="abs hero-btn"></div>

<div class="abs tile tile-1" role="img" aria-label="Hände halten reife Weizenähren"></div>
<div class="abs tile tile-2" role="img" aria-label="Strohballen auf einem Feld"></div>
<div class="abs tile tile-3" role="img" aria-label="Nahaufnahme goldener Weizenähren"></div>

<h2 class="abs intro-title">Excepteur sint occaecat cupidatat non proident, sunt in culpa</h2>
<svg class="abs intro-box" width="192" height="96" viewBox="0 0 192 96"><polygon points="26,0 192,0 192,96 26,96 0,48" fill="#f3cc1f"/></svg>
<div class="abs intro-text">
  <p>Sed ut perspiciatis unde omnis iste natus error sit voluptatem accusantium doloremque laudantium, to</p>
  <p>Sed ut perspiciatis unde omnis iste natus error sit voluptatem accusantium doloremque laudantium, to</p>
</div>

<svg class="abs why-bg" width="688" height="268" viewBox="0 0 688 268"><polygon points="0,0 688,0 688,267 0,177" fill="#232323"/></svg>
<h2 class="abs why-title">Warum Uns Wählen?</h2>
<p class="abs why-lead">Excepteur sint occaecat cupidatat non proident, sunt in culpa qui officia deserunt mollit anim id es</p>
<div class="abs feature" style="left:165px;top:552px"><span class="dot"></span><h3>Lorem Ipsum</h3><p>Excepteur sint occaecat cupidatat non proident, sunt in culpa</p></div>
<div class="abs feature" style="left:271px;top:552px"><span class="dot"></span><h3>Lorem Ipsum</h3><p>Excepteur sint occaecat cupidatat non proident, sunt in culpa</p></div>
<div class="abs feature" style="left:165px;top:596px"><span class="dot"></span><h3>Lorem Ipsum</h3><p>Excepteur sint occaecat cupidatat non proident, sunt in culpa</p></div>
<div class="abs feature" style="left:271px;top:596px"><span class="dot"></span><h3>Lorem Ipsum</h3><p>Excepteur sint occaecat cupidatat non proident, sunt in culpa</p></div>
<div class="abs why-btn"></div>
<div class="abs why-frame"></div>
<div class="abs why-photo" role="img" aria-label="Mähdrescher bei der Weizenernte im Sonnenuntergang"></div>

<h2 class="abs testi-title">Die Leute Sagen Über Uns</h2>
<svg class="abs testi-svg" width="688" height="120" viewBox="0 0 688 120">
  <path d="M0,27 L82,12 Q99,10 99,30 L99,100 Q99,118 82,118 L0,118 Z" fill="#f3cc1f"/>
  <path d="M185,18 L500,-15 Q519,-17 519,5 L519,100 Q519,117 500,117 L187,117 Q167,117 167,100 L167,40 Q167,20 185,18 Z" fill="#f3cc1f"/>
  <path d="M688,22 L600,46 Q582,52 582,68 L582,100 Q582,117 600,117 L688,117 Z" fill="#f3cc1f"/>
</svg>
<div class="abs testi-text">
  <p>Sed ut perspiciatis unde omnis iste natus error sit voluptatem accusantium doloremque laudantium, to</p>
  <p>Sed ut perspiciatis unde omnis iste natus error sit voluptatem accusantium doloremque laudantium, to</p>
</div>
<div class="abs avatar" style="left:30px;top:768px" role="img" aria-label="Porträt eines Kunden"></div>
<div class="abs avatar" style="left:455px;top:767px" role="img" aria-label="Porträt einer Kundin"></div>
<div class="abs pager current" style="left:280px"></div>
<div class="abs pager" style="left:326px"></div>
<div class="abs pager" style="left:373px"></div>

<footer class="abs footer"></footer>
<div class="abs vline" style="left:204px"></div>
<div class="abs vdot" style="left:202px;top:1015px"></div>
<div class="abs vdot" style="left:202px;top:1097px"></div>
<div class="abs vline" style="left:483px"></div>
<div class="abs vdot" style="left:481px;top:1015px"></div>
<div class="abs vdot" style="left:481px;top:1097px"></div>
<h2 class="abs contact-title">Kontak Uns</h2>
<div class="abs field" style="left:226px;top:1042px;width:73px">Name</div>
<div class="abs field" style="left:307px;top:1042px;width:73px">Email</div>
<div class="abs field" style="left:389px;top:1042px;width:73px">Telefonnummer</div>
<div class="abs field" style="left:226px;top:1065px;width:154px;height:19px;padding-top:7px">Nachricht</div>
<div class="abs send">Schicken</div>
<ul class="abs info">
  <li><svg width="6" height="7" viewBox="0 0 6 8"><path d="M3,0 A3,3 0 0 1 6,3 C6,5 3,8 3,8 C3,8 0,5 0,3 A3,3 0 0 1 3,0 Z" fill="#fff"/><circle cx="3" cy="3" r="1.1" fill="#232323"/></svg>Locatins</li>
  <li><svg width="7" height="7" viewBox="0 0 8 8"><circle cx="4" cy="4" r="4" fill="#fff"/><path d="M2.5,2 L3.4,2 L3.8,3.2 L3.2,3.7 Q3.8,4.8 4.6,5.1 L5.1,4.5 L6.2,4.9 L6.2,5.8 Q4.5,6.3 3,4.8 Q1.8,3.4 2.5,2 Z" fill="#232323"/></svg>+49 0000 482715</li>
  <li><svg width="7" height="6" viewBox="0 0 8 6"><rect width="8" height="6" fill="#fff"/><path d="M0,0 L4,3.3 L8,0" fill="none" stroke="#232323" stroke-width=".8"/></svg>info@kornhaus-agrar.example</li>
</ul>
<div class="abs foot-brand">Kornhaus</div>
<div class="abs social" style="left:318px"></div>
<div class="abs social" style="left:332px"></div>
<div class="abs social" style="left:346px"></div>
<div class="abs social" style="left:359px"></div>
<div class="abs copy">Copyright 2023 All Right Reserved</div>

</body>
</html>
```